Business card design for a dynamic IT consulting company

We need a business card design for a young firm, specialized in the Telecommunications/Consulting industry. The name of the company is Quindor and Partners Business Consulting Ltd. (Short name: Quindor and Partnes)
Quindor = solve read reverse, so we aim to be uncomplicated and solution-oriented. The small pipe in our logo is also related to the word solve. So we need a new business card design, which is simple, eye catching and something non traditional (I would probably prefer a square shaped design rather than a rectangle, but open for suggestions). Attached our logo.

Target Market(s)

Usually our customers are Tier1 Telecoms providers (Q-Netra, Palorix, etc) and their executives.

Industry/Entity Type

Business

Contact Information for Business Card

Name: Bence Tolnavari
Email: b.tolnavari@quindor.hu
Web: www.quindor.hu
Mobile: +36 30 518 2769
Title: Managing Director

Optional:
Company name: Quindor and Partners Ltd.
Address: 1087 Budapest, Tolvenka str. 28/C, Hungary

Font styles to use
Other font styles liked:
• helveticaneue_medium, Prime Regular are used now.

Colors

Designer to choose colors to be used in the design.

Requirements
Must have
• I would like to have a 2 sided design.
Nice to have
• I thought if we make the logo a bit bigger (without the company name), that could go to the back with the company name below. I though, if the pipe in the logo is somehow touchable on the business card, would be nice and unique.

```html
<!DOCTYPE html>
<html lang="en">
<head>
<meta charset="utf-8">
<title>Quindor &amp; Partners – Business Card</title>
<link href="https://fonts.googleapis.com/css2?family=Exo+2:wght@400;500&family=Work+Sans:wght@400&display=swap" rel="stylesheet">
<style>
  :root {
    --stage: #161616;
    --paper: #ffffff;
    --magenta: #bb2f8f;
    --blue: #1b8fd8;
    --ink: #4a4a4a;
    --ink-soft: #5a5a5a;
    --white: #ffffff;
  }
  * { margin: 0; padding: 0; box-sizing: border-box; }
  html, body {
    width: 1200px; height: 897px; overflow: hidden;
    background: var(--stage);
  }
  .canvas { position: relative; width: 1200px; height: 897px; }

  .card {
    position: absolute; left: 303px; width: 595px; height: 339px;
  }
  .card--front { top: 92px; background: var(--paper); }
  .card--back { top: 469px; background: var(--magenta); }

  /* Wordmark */
  .wordmark {
    position: absolute; display: flex; align-items: center;
    font-family: "Exo 2", sans-serif; font-weight: 400; white-space: nowrap;
  }
  .wordmark__square { display: block; flex: none; }
  .card--front .wordmark { left: 24px; top: 146px; gap: 10px; font-size: 26px; color: var(--ink); }
  .card--front .wordmark__square { width: 14px; height: 14px; background: var(--magenta); }
  .card--back .wordmark { left: 0; right: 0; top: 138px; justify-content: center; gap: 16px; font-size: 50px; color: var(--white); }
  .card--back .wordmark__square { width: 26px; height: 26px; background: var(--white); }

  /* Contact block */
  .divider {
    position: absolute; left: 303px; top: 87px; width: 2px; height: 166px;
    background: var(--magenta);
  }
  .contact { position: absolute; left: 330px; top: 84px; font-family: "Work Sans", sans-serif; color: var(--ink-soft); }
  .contact__name {
    font-family: "Exo 2", sans-serif; font-weight: 400; font-size: 21px;
    color: var(--blue); letter-spacing: 0.5px; line-height: 1.2;
  }
  .contact__title { font-size: 14px; margin-top: 4px; }
  .contact__company {
    font-family: "Exo 2", sans-serif; font-weight: 500; font-size: 14px;
    color: var(--blue); margin-top: 13px; letter-spacing: 0.3px;
  }
  .contact__address { font-size: 13.5px; line-height: 17px; margin-top: 2px; }
  .contact__lines { list-style: none; margin-top: 10px; }
  .contact__line { display: flex; align-items: center; gap: 12px; font-size: 13.5px; height: 19.5px; }
  .contact__icon { width: 11px; height: 11px; flex: none; fill: var(--blue); }

  .web {
    position: absolute; left: 0; right: 0; top: 295px; text-align: center;
    font-family: "Work Sans", sans-serif; font-size: 15px; letter-spacing: 2px;
    color: var(--white);
  }
</style>
</head>
<body>
<main class="canvas">
  <section class="card card--front" aria-label="Card front">
    <div class="wordmark"><span class="wordmark__square"></span>Quindor &amp; Partners</div>
    <div class="divider"></div>
    <div class="contact">
      <h1 class="contact__name">BENCE TOLNAVARI</h1>
      <p class="contact__title">Managing Director</p>
      <p class="contact__company">QUINDOR AND PARTNERS LTD.</p>
      <p class="contact__address">1087 Budapest, Tolvenka<br>str. 28/C, Hungary</p>
      <ul class="contact__lines">
        <li class="contact__line">
          <svg class="contact__icon" viewBox="0 0 24 24" aria-hidden="true"><path d="M6.6 10.8a15 15 0 0 0 6.6 6.6l2.2-2.2c.3-.3.7-.4 1-.2 1.1.4 2.3.6 3.6.6.6 0 1 .4 1 1V20c0 .6-.4 1-1 1A17 17 0 0 1 3 4c0-.6.4-1 1-1h3.5c.6 0 1 .4 1 1 0 1.3.2 2.5.6 3.6.1.3 0 .7-.2 1z"/></svg>
          +36 30 518 2769
        </li>
        <li class="contact__line">
          <svg class="contact__icon" viewBox="0 0 24 24" aria-hidden="true"><path d="M2 5h20v14H2z M2 5l10 8 10-8" fill="var(--blue)"/><path d="M3 6l9 7 9-7" fill="none" stroke="#fff" stroke-width="1.6"/></svg>
          b.tolnavari@quindor.hu
        </li>
        <li class="contact__line">
          <svg class="contact__icon" viewBox="0 0 24 24" aria-hidden="true"><circle cx="12" cy="12" r="10" fill="none" stroke="var(--blue)" stroke-width="2"/><ellipse cx="12" cy="12" rx="4.5" ry="10" fill="none" stroke="var(--blue)" stroke-width="1.6"/><path d="M2 12h20M4 7h16M4 17h16" stroke="var(--blue)" stroke-width="1.4"/></svg>
          www.quindor.hu
        </li>
      </ul>
    </div>
  </section>

  <section class="card card--back" aria-label="Card back">
    <div class="wordmark"><span class="wordmark__square"></span>Quindor &amp; Partners</div>
    <p class="web">www.quindor.hu</p>
  </section>
</main>
</body>
</html>
```